Sleek wordpress site for Bramblecrest finishing works

We are a commercial job shop that serves B2B, govt & LEO and retail clients.We need a wordpress site with 6 individual pages: homepage, coating, laser engraving, laser cutting, part marking, and contact us. I have attached an outline of the desired flow and sub headings for each page. I would like to incorporate the colors of the logo through out the site to be clean and sleek enough to appeal to B2B commercial clients yet be inviting enough for retail clients.

I would like to have easy picture functionality so photographs on each page can be updated easily.

Target Market(s)

B2B industrial & Govt and Military part marking, laser engraving and coating: machine shops, aerospace companies, tool manufactures. Retail: personalized gifts, Job Shop

Coding

Coded - Design and coding required

Font styles to use
Sans Serif
Other font styles liked:
• Open to suggestion

Colors
0255a3
3176b5
eaf1f7
cfdeed
ffffff

Requirements
Must have
• Clean easy to navigate flow, separate pages as indicated on attached outline, high class feel. Great picture functionality, professional and inviting feel,
• **update: needs to be optimized for mobile, should have a gallery function. Gallery can be an additional page or embedded
Nice to have
• Social media connectivity links,
Should not have
• crappy plugins that make back-end management difficult, no blog

```html
<!DOCTYPE html>
<html lang="en">
<head>
<meta charset="utf-8">
<title>Bramblecrest Finishing Works</title>
<link rel="stylesheet" href="https://fonts.googleapis.com/css2?family=Michroma&family=Ubuntu:wght@400;500;700&family=Lato:ital,wght@0,400;0,700;1,400&display=swap">
<style>
:root{
  --brand:#0255a3;
  --brand-mid:#3176b5;
  --brand-pale:#eaf1f7;
  --brand-soft:#cfdeed;
  --white:#ffffff;
  --panel:#f3f3f3;
  --ink:#1f4f94;
  --body:#7a7a7a;
  --field:#3a78b8;
}
*{box-sizing:border-box;margin:0;padding:0}
html,body{width:1200px;height:3681px;overflow:hidden}
body{font-family:"Lato",sans-serif;color:var(--body);background:var(--white)}
.btn{display:inline-block;background:var(--brand);color:var(--white);font-family:"Ubuntu",sans-serif;font-size:20px;border-radius:30px;padding:0 28px;height:60px;line-height:60px;box-shadow:0 3px 0 rgba(0,0,0,.25);text-decoration:none}
.lede{font-size:13.5px;line-height:25px}

/* header */
.site-header{position:relative;height:135px;background:var(--brand-mid)}
.topbar{position:absolute;right:78px;top:0;height:52px;display:flex;align-items:center;gap:14px;color:var(--white);font-size:14px}
.topbar .social{display:flex;gap:10px;padding-right:16px;border-right:1px solid rgba(255,255,255,.4);height:52px;align-items:center}
.topbar .social span{width:10px;height:10px;border-radius:50%;background:var(--white)}
.topbar .account{padding-left:4px}
.header-rule{position:absolute;left:300px;right:78px;top:52px;border-top:1px solid rgba(255,255,255,.3)}
.brand{position:absolute;left:78px;top:0;width:207px;height:172px;background:var(--white);clip-path:polygon(0 0,100% 0,100% 80%,50% 100%,0 80%);display:flex;flex-direction:column;align-items:center;justify-content:center;gap:10px;padding:0 16px 20px;z-index:2}
.brand .mark{width:26px;height:26px;background:var(--brand)}
.brand .name{font-family:"Ubuntu",sans-serif;font-weight:700;font-size:15px;color:var(--brand);text-align:center;line-height:19px;text-transform:uppercase}
.main-nav{position:absolute;left:319px;top:80px;display:flex;gap:24px;font-family:"Ubuntu",sans-serif;font-size:16px;color:var(--white);text-transform:uppercase}
.main-nav .current{font-weight:700}
.nav-tools{position:absolute;left:1043px;top:76px;display:flex;gap:24px}

/* hero */
.hero{position:relative;height:572px;background:linear-gradient(160deg,#3a3c42 0%,#26272b 40%,#5b4330 75%,#c98a3c 100%);text-align:center;color:var(--white)}
.hero h1{position:absolute;top:120px;left:0;right:0;font-family:"Michroma",sans-serif;font-weight:400;font-size:38px;line-height:50px;text-transform:uppercase;letter-spacing:1px;text-shadow:0 2px 6px rgba(0,0,0,.5)}
.hero p{position:absolute;top:235px;left:290px;right:290px;font-size:15px;line-height:25px}
.hero .btn{position:absolute;top:326px;left:514px;height:57px;line-height:57px;font-size:19px}
.dots{position:absolute;top:482px;left:0;right:0;display:flex;justify-content:center;gap:11px}
.dots span{width:18px;height:18px;border:2px solid var(--white);border-radius:50%}
.dots .on{background:var(--white)}

/* why */
.why{height:388px;text-align:center;padding-top:60px}
.section-title{display:flex;align-items:center;justify-content:center;gap:26px;font-family:"Ubuntu",sans-serif;font-weight:500;font-size:34px;color:var(--ink)}
.section-title::before,.section-title::after{content:"";width:86px;border-top:1px solid #bbb}
.why .lede{width:640px;margin:30px auto 0}
.why .btn{margin-top:38px}

/* services */
.service{display:flex;height:417px}
.service-text{width:600px;padding:64px 0 0 78px;background:var(--panel)}
.service.alt .service-text{background:var(--brand-mid);color:var(--white);padding-left:26px;padding-right:40px}
.service.alt .service-text h2{color:var(--white)}
.service-text h2{display:flex;align-items:center;gap:22px;font-family:"Ubuntu",sans-serif;font-weight:500;font-size:34px;color:var(--ink)}
.service-text h2::after{content:"";width:86px;border-top:1px solid currentColor;opacity:.5}
.service-text .lede{margin-top:24px;width:490px}
.service-text .btn{margin-top:38px}
.service-photo{width:600px}

/* newsletter */
.newsletter{height:309px;text-align:center;padding-top:60px}
.newsletter .tag{margin-top:20px;font-style:italic;font-size:15px}
.sub-form{margin:38px auto 0;width:674px;height:61px;display:flex;border-radius:31px;box-shadow:0 2px 10px rgba(0,0,0,.15);overflow:hidden}
.sub-form .input{flex:1;display:flex;align-items:center;gap:10px;padding-left:24px;font-style:italic;font-size:15px;color:#666}
.sub-form .go{width:160px;background:var(--brand);color:var(--white);font-family:"Ubuntu",sans-serif;font-size:18px;display:flex;align-items:center;justify-content:center}

/* contact */
.contact{position:relative;height:609px;background:linear-gradient(var(--white) 0 59px,var(--brand) 59px)}
.info-bar{position:absolute;left:78px;right:76px;top:5px;height:103px;background:var(--brand-mid);box-shadow:0 3px 8px rgba(0,0,0,.3);display:flex;align-items:center;color:var(--white);font-family:"Ubuntu",sans-serif;font-size:16px;font-weight:500;padding-left:10px}
.info-item{display:flex;align-items:center;gap:14px;margin-right:50px;line-height:22px}
.info-item .ic{width:40px;height:40px;border-radius:50%;background:var(--white);display:flex;align-items:center;justify-content:center}
.info-social{margin-left:auto;margin-right:26px;display:flex;gap:12px}
.info-social span{width:40px;height:40px;border:2px solid rgba(255,255,255,.8);border-radius:50%}
.contact .section-title{position:absolute;top:168px;left:0;right:0;color:var(--white)}
.contact .section-title::before,.contact .section-title::after{border-color:rgba(255,255,255,.5)}
.form{position:absolute;left:200px;top:246px;width:800px;display:grid;grid-template-columns:repeat(3,1fr);gap:14px 12px;font-size:13px;color:var(--white)}
.field{background:var(--field);height:59px;padding:19px 12px}
.field.message{grid-column:1/4;height:99px}
.contact .submit{position:absolute;top:432px;left:518px;background:var(--white);color:var(--brand);font-family:"Ubuntu",sans-serif;font-size:19px;font-weight:500;border-radius:30px;height:59px;line-height:59px;padding:0 20px}
.copyright{position:absolute;left:0;right:0;top:535px;border-top:1px solid rgba(255,255,255,.3);padding-top:27px;text-align:center;font-size:14px;color:var(--white)}
.copyright b{font-weight:700}
</style>
</head>
<body>

<header class="site-header">
  <div class="brand"><span class="mark"></span><span class="name">Bramblecrest finishing works</span></div>
  <div class="topbar">
    <div class="social"><span></span><span></span><span></span><span></span></div>
    <div class="account">Login or Register</div>
  </div>
  <div class="header-rule"></div>
  <nav class="main-nav">
    <span class="current">Home</span><span>Coating</span><span>Laser Engraving</span><span>Lesar Cutting</span><span>Part Marketing</span><span>Contact</span>
  </nav>
  <div class="nav-tools">
    <svg width="20" height="22" viewBox="0 0 20 22"><circle cx="8" cy="8" r="6" fill="none" stroke="#fff" stroke-width="2"/><line x1="12.5" y1="12.5" x2="18" y2="18" stroke="#fff" stroke-width="2.5"/></svg>
    <svg width="26" height="24" viewBox="0 0 26 24"><path d="M1 6h4l3 11h11l3-8H7" fill="none" stroke="#fff" stroke-width="2"/><circle cx="10" cy="21" r="2" fill="#fff"/><circle cx="18" cy="21" r="2" fill="#fff"/><circle cx="21" cy="5" r="5" fill="#fff"/></svg>
  </div>
</header>

<section class="hero" role="img" aria-label="Workshop photo of sparks flying from metal grinding">
  <h1>Bramblecrest<br>Finishing Works</h1>
  <p>Lorem Ipsum is simply dummy text of the printing and typesetting industry. Lorem Ipsum has been the industry's standard dummy text ever since the 1500s.</p>
  <a class="btn">CONTACT US</a>
  <div class="dots"><span></span><span class="on"></span><span></span></div>
</section>

<section class="why">
  <h2 class="section-title">Why Choose Us?</h2>
  <p class="lede">Lorem Ipsum is simply dummy text of the printing and typesetting industry. Lorem Ipsum has been the industry's standard dummy text ever since the 1500s, when an unknown printer took a galley of type and scrambled it to make a type specimen book. It has survived not only five centuries, but also the leap into electronic typesetting, remaining essentially unchanged.</p>
  <a class="btn">READ MORE</a>
</section>

<section class="service">
  <div class="service-text">
    <h2>Coating</h2>
    <p class="lede">Lorem Ipsum is simply dummy text of the printing and typesetting industry. Lorem Ipsum has been the industry's standard dummy text ever since the 1500s, when an unknown printer took a galley of type and scrambled it to make a type specimen book. It has survived not only five centuries, but also the leap into electronic typesetting, remaining essentially unchanged.</p>
    <a class="btn">READ MORE</a>
  </div>
  <div class="service-photo" role="img" aria-label="Torch heating a coated surface" style="background:linear-gradient(135deg,#5a4a44,#2b2623 55%,#8a5a3a)"></div>
</section>

<section class="service alt">
  <div class="service-photo" role="img" aria-label="Laser engraving machine head over a work plate" style="background:linear-gradient(135deg,#8d8f94,#3c3e44 50%,#b9ab92)"></div>
  <div class="service-text">
    <h2>Laser Engraving</h2>
    <p class="lede">Lorem Ipsum is simply dummy text of the printing and typesetting industry. Lorem Ipsum has been the industry's standard dummy text ever since the 1500s, when an unknown printer took a galley of type and scrambled it to make a type specimen book. It has survived not only five centuries, but also the leap into electronic typesetting, remaining essentially unchanged.</p>
    <a class="btn">READ MORE</a>
  </div>
</section>

<section class="service">
  <div class="service-text">
    <h2>Lesar Cutting</h2>
    <p class="lede">Lorem Ipsum is simply dummy text of the printing and typesetting industry. Lorem Ipsum has been the industry's standard dummy text ever since the 1500s, when an unknown printer took a galley of type and scrambled it to make a type specimen book. It has survived not only five centuries, but also the leap into electronic typesetting, remaining essentially unchanged.</p>
    <a class="btn">READ MORE</a>
  </div>
  <div class="service-photo" role="img" aria-label="Laser cutter slicing a steel sheet" style="background:linear-gradient(135deg,#4f6a86,#22344a 55%,#a07a52)"></div>
</section>

<section class="service alt">
  <div class="service-photo" role="img" aria-label="Technician inspecting a part at a marking station" style="background:linear-gradient(135deg,#d7dde4,#7f8a98 60%,#3b4656)"></div>
  <div class="service-text">
    <h2>Part Marketing</h2>
    <p class="lede">Lorem Ipsum is simply dummy text of the printing and typesetting industry. Lorem Ipsum has been the industry's standard dummy text ever since the 1500s, when an unknown printer took a galley of type and scrambled it to make a type specimen book. It has survived not only five centuries, but also the leap into electronic typesetting, remaining essentially unchanged.</p>
    <a class="btn">READ MORE</a>
  </div>
</section>

<section class="newsletter">
  <h2 class="section-title">Subscribe Newsletter</h2>
  <p class="tag">Lorem Ipsum is simply dummy text of the printing and typesetting industry.</p>
  <div class="sub-form">
    <div class="input"><svg width="16" height="12" viewBox="0 0 16 12"><rect width="16" height="12" fill="#0255a3"/><path d="M0 0l8 6 8-6" fill="none" stroke="#fff" stroke-width="1.5"/></svg>Enter Email :</div>
    <div class="go">SUBSCRIBE</div>
  </div>
</section>

<section class="contact">
  <div class="info-bar">
    <div class="info-item"><span class="ic"><svg width="16" height="20" viewBox="0 0 16 20"><path d="M8 0a7 7 0 0 0-7 7c0 5 7 13 7 13s7-8 7-13a7 7 0 0 0-7-7z" fill="#0255a3"/><circle cx="8" cy="7" r="2.5" fill="#fff"/></svg></span>418 W Alder Row #7,<br>Tempe, AZ 85281</div>
    <div class="info-item"><span class="ic"><svg width="18" height="18" viewBox="0 0 18 18"><path d="M4 1l3 4-2 2c1 2 4 5 6 6l2-2 4 3-2 3C8 17 1 10 1 3z" fill="#0255a3"/></svg></span>480.555.0147</div>
    <div class="info-item"><span class="ic"><svg width="18" height="14" viewBox="0 0 18 14"><rect width="18" height="14" fill="#0255a3"/><path d="M0 0l9 7 9-7" fill="none" stroke="#fff" stroke-width="1.5"/></svg></span>hello@bramblecrest.com</div>
    <div class="info-social"><span></span><span></span><span></span><span></span></div>
  </div>
  <h2 class="section-title">Contact Us</h2>
  <div class="form">
    <div class="field">Enter Name :</div>
    <div class="field">Phone :</div>
    <div class="field">Email :</div>
    <div class="field message">Message :</div>
  </div>
  <div class="submit">SUBMIT NOW</div>
  <p class="copyright">Copyright © <b>BRAMBLECREST FINISHING WORKS</b> - 2018 . All Right Reserved</p>
</section>

</body>
</html>
```